Brightway Haul & Upkeep Services, are a company that offers a 'one stop shop' pre-move clean up a

I have already selected a logo which I would like on the front of the business cards along with phone numbers, web address and email which are:
0487650392
www.brightwayhaul.com.au
brightwayhaulandupkeep@mailbox.example

On the back of the card I would like to list some of the types of service we offer (clean - move - repairs/maintenance) which are:
CLEAN - windows, gutters, solar panels, driveways/paths, carpets.
MOVE - Small/medium size house/office moves, large item pick-up & delivery, yard clean-up and removal.
General maintenance and repairs.

I would like the blue logo on a gray background.

Thanks

```html
<!DOCTYPE html>
<html lang="en">
<head>
<meta charset="utf-8">
<title>Brightway Haul &amp; Upkeep Services – Business Cards</title>
<link rel="stylesheet" href="https://fonts.googleapis.com/css2?family=Open+Sans:wght@400;600;700&display=swap">
<style>
  :root {
    --brand-blue: #1f6db5;
    --sky-blue: #7dbde8;
    --ink: #1d1d1b;
    --paper: #ffffff;
    --backdrop: #d9dadc;
  }
  * { box-sizing: border-box; margin: 0; padding: 0; }
  html, body { width: 1200px; height: 393px; overflow: hidden; }
  body {
    background: var(--backdrop);
    font-family: "Open Sans", Arial, sans-serif;
    color: var(--ink);
    position: relative;
  }
  .card {
    position: absolute;
    background: var(--paper);
    border-radius: 20px;
    overflow: hidden;
    box-shadow: 0 2px 6px rgba(0,0,0,.18);
  }
  .card--front { left: 38px; top: 37px; width: 546px; height: 311px; }
  .card--back  { left: 622px; top: 40px; width: 544px; height: 310px; }

  .header-band {
    position: absolute; left: 0; top: 0; width: 100%; height: 92px;
    background: linear-gradient(180deg, var(--brand-blue) 0%, var(--brand-blue) 70%, var(--sky-blue) 100%);
  }

  .phone {
    position: absolute; top: 22px; right: 36px;
    display: flex; align-items: center; gap: 6px;
    color: var(--paper); font-size: 19px; letter-spacing: .3px;
  }
  .phone svg { width: 17px; height: 17px; }

  .brand-name {
    color: var(--brand-blue);
    font-weight: 700;
    text-transform: uppercase;
    line-height: 1.05;
    display: flex; align-items: center; gap: 12px;
  }
  .brand-name .mark {
    width: 18px; height: 18px; border-radius: 50%;
    background: var(--brand-blue); flex: none;
  }
  .brand-name small { display: block; font-size: .62em; }
  .card--front .brand-name {
    position: absolute; left: 30px; top: 134px; font-size: 34px;
  }
  .card--back .brand-name {
    position: absolute; left: 0; right: 0; top: 84px;
    justify-content: center; font-size: 36px; text-align: center;
  }

  .contacts {
    position: absolute; left: 28px; top: 244px;
    list-style: none; font-size: 15px; line-height: 22px;
  }
  .contacts li { display: flex; align-items: center; gap: 8px; }
  .contacts svg { width: 12px; height: 12px; flex: none; }

  .services-title {
    position: absolute; left: 0; right: 0; top: 186px;
    text-align: center; color: var(--brand-blue);
    font-size: 20px; font-weight: 700; letter-spacing: 2px;
  }
  .services-list {
    position: absolute; left: 0; right: 0; top: 230px;
    text-align: center; font-size: 16px; font-weight: 600; line-height: 28px;
  }
  .services-list .bullet { color: var(--brand-blue); margin-right: 5px; }
  .services-list .gap { display: inline-block; width: 16px; }
</style>
</head>
<body>
  <section class="card card--front" aria-label="Business card front">
    <div class="header-band" role="img" aria-label="Decorative blue swoosh band across the top of the card"></div>

    <div class="phone">
      <svg viewBox="0 0 24 24" fill="none" stroke="#fff" stroke-width="2"><circle cx="12" cy="12" r="10"/><path d="M8 7l2 3-1 1c1 2 2 3 4 4l1-1 3 2-1 2c-4 0-9-5-9-9z" fill="#fff" stroke="none"/></svg>
      <span>0487650392</span>
    </div>

    <h1 class="brand-name"><span class="mark"></span><span>Brightway Haul<small>&amp; Upkeep Services</small></span></h1>

    <ul class="contacts">
      <li><svg viewBox="0 0 12 12"><rect x="0" y="2" width="12" height="8" rx="1.5" fill="#1f6db5"/><path d="M1 3l5 4 5-4" stroke="#fff" fill="none"/></svg>brightwayhaulandupkeep@mailbox.example</li>
      <li><svg viewBox="0 0 12 12"><circle cx="6" cy="6" r="5.5" fill="#1f6db5"/><path d="M0.5 6h11M6 .5c-3 3-3 8 0 11M6 .5c3 3 3 8 0 11" stroke="#fff" stroke-width=".8" fill="none"/></svg>www.brightwayhaul.com.au</li>
    </ul>
  </section>

  <section class="card card--back" aria-label="Business card back">
    <h2 class="brand-name"><span class="mark"></span><span>Brightway Haul<small>&amp; Upkeep Services</small></span></h2>
    <p class="services-title">Services we offer</p>
    <div class="services-list">
      <div><span class="bullet">•</span>Clean<span class="gap"></span><span class="bullet">•</span>Move</div>
      <div><span class="bullet">•</span>General Maintenance And Repairs.</div>
    </div>
  </section>
</body>
</html>
```